Front and back cover design for skincare marketing materials

Thank you for showing an interest in my project.
Project Details.

I require a front and back cover for our marketing materials.
·       Front Cover size: 105 mm W x 150 mm H.
·       Back Cover size:  105 mm W x 150 mm H.
·       It must include these two colors. You can use a third color if you wish.
1.     #DBA09D
2.     #FFFFFF
 
Front Cover
·      The front cover will have a faded image of the Kakadu Plum branch and fruit. There are two image files, KP_image-1.jpg and kp_image-2.jpeg. You can use both images, just a portion of them, or source alternative royalty-free images of Kakadu Plum that may better fit the design. These two files have been uploaded.
 
The front cover wording.
Top of the front cover.
a.     The title of the image. “Kakadu Plum”
b.     The brand name, “Vellora Skincare”. The file brand_name.ai uploaded.
 
Bottom of the front cover- Designer's choice of font.
The bottom of the front cover contains three lines of text in the following order.  
1.     Australian Native Ingredients
2.     100% Natural · Organic · Wild-harvested
3.     Australian-Made Premium Skincare
 
Back Cover
·      Back Cover wording.The back cover contains the following words "grown by nature" in white (#FFFFFF) of font Italianno (font_file.ttf) with a background color of #DBA09D as seen in the sample box (sample_box.pdf) right-side panel
 
Please provide one file for the front cover and a separate file for the back cover.
All the elements of the files must be editable.
 
Do NOT use the Curve function on the files, as the text must remain editable/changeable.
 
All assets/resources/files, including fonts not supplied by us but used by the designer, must be named and provided with the finished design.
Updates

Slow to provide project details.

Target Market(s)

Beauty-minded Asian consumers between the ages of 32 and 75 who take a proactive approach to maintaining younger-looking skin. Those who already know the danger of skin damage caused by skincare containing harsh chemicals choose effective natural/organic solutions to meet their skincare needs. Those who wish a more radiant glow and youthful appearance to their skin. Usually, a two-income middle to high-income bracket couples with a mindset for health and beauty.

Industry/Entity Type

beauty

Font styles to use
Other font styles liked:
• I will provide a font file and a brand name file.

Requirements
Must have
• You must use the two colors provided on the product box. The designer may use a third color.
Nice to have
• some gold colour

```html
<!DOCTYPE html>
<html lang="en">
<head>
<meta charset="utf-8">
<title>Vellora Skincare – Cover Dieline N0.2</title>
<link rel="stylesheet" href="https://fonts.googleapis.com/css2?family=Italianno&family=Poppins:wght@400;500&family=Roboto:wght@700&display=swap">
<style>
  :root {
    --stage-bg: #cfd1b3;
    --panel-white: #ffffff;
    --brand-pink: #d98dac;
    --logo-pink: #dc93b2;
    --ink: #000000;
    --text-dark: #1d1d1d;
    --leaf-light: #a9cf7a;
    --leaf-dark: #4f7c2e;
  }
  * { margin: 0; padding: 0; box-sizing: border-box; }
  html, body { width: 1200px; height: 892px; overflow: hidden; background: var(--stage-bg); }
  .stage { position: relative; width: 1200px; height: 892px; background: var(--stage-bg); }

  .sheet-number {
    position: absolute; left: 44px; top: 34px;
    font-family: "Roboto", Arial, sans-serif; font-weight: 700; font-size: 40px; color: var(--ink);
  }

  .guides { position: absolute; left: 0; top: 0; width: 1200px; height: 892px; }

  .label {
    position: absolute;
    font-family: "Roboto", Arial, sans-serif; font-weight: 700; color: var(--ink); line-height: 1.2;
  }
  .label--top { left: 171px; top: 346px; font-size: 30px; }
  .label--front { left: 158px; top: 569px; font-size: 50px; line-height: 1.28; }
  .label--back { left: 857px; top: 569px; font-size: 50px; }

  .panel { position: absolute; }
  .panel--top-fold {
    left: 326px; top: 71px; width: 253px; height: 378px;
    background: var(--panel-white);
    border-radius: 126.5px 126.5px 0 0;
  }
  .panel--front {
    left: 326px; top: 449px; width: 253px; height: 361px;
    background: var(--panel-white);
  }
  .panel--back {
    left: 578px; top: 449px; width: 253px; height: 361px;
    background: var(--brand-pink);
  }

  .wordmark {
    position: absolute; left: 0; width: 100%; text-align: center;
    font-family: "Poppins", Arial, sans-serif; font-weight: 500; font-size: 23px;
    color: var(--logo-pink); letter-spacing: 0.5px;
  }
  .panel--top-fold .wordmark { top: 257px; }
  .panel--front .wordmark { top: 82px; }

  .product-title {
    position: absolute; left: 0; top: 33px; width: 100%; text-align: center;
    font-family: "Poppins", Arial, sans-serif; font-weight: 400; font-size: 30px;
    color: var(--ink); letter-spacing: 0.3px;
  }

  .product-photo {
    position: absolute; left: 45px; top: 190px; width: 163px; height: 54px;
    background: linear-gradient(90deg, var(--leaf-dark) 0%, var(--leaf-light) 45%, #8fbf72 55%, #b9dc9a 100%);
  }

  .claims {
    position: absolute; left: 0; top: 299px; width: 100%; text-align: center;
    font-family: "Poppins", Arial, sans-serif; font-weight: 500; font-size: 10.3px;
    line-height: 14.6px; color: var(--text-dark);
  }

  .tagline {
    position: absolute; left: 50%; top: 50%;
    transform: translate(-50%, -50%) rotate(-90deg);
    white-space: nowrap;
    font-family: "Italianno", cursive; font-size: 58px; line-height: 1;
    color: var(--panel-white);
  }
</style>
</head>
<body>
<main class="stage">
  <div class="sheet-number">N0.2</div>

  <section class="panel panel--top-fold">
    <div class="wordmark">Vellora Skincare</div>
  </section>

  <section class="panel panel--front">
    <h1 class="product-title">Kakadu Plum</h1>
    <div class="wordmark">Vellora Skincare</div>
    <div class="product-photo" role="img" aria-label="Kakadu Plum branch with green fruit and leaves"></div>
    <p class="claims">
      Australian Native Ingredients<br>
      100% Natural · Organic · Wild-harvested<br>
      Australian-Made Premium Skincare
    </p>
  </section>

  <section class="panel panel--back">
    <p class="tagline">grown by nature</p>
  </section>

  <svg class="guides" viewBox="0 0 1282 953" aria-hidden="true">
    <g fill="none" stroke="#000" stroke-width="5">
      <polyline points="237,370 237,301 300,301"/>
      <polyline points="237,609 237,543 300,543"/>
      <polyline points="996,609 996,543 934,543"/>
    </g>
    <g fill="#000">
      <polygon points="313,301 296,292 296,310"/>
      <polygon points="313,543 296,534 296,552"/>
      <polygon points="920,543 937,534 937,552"/>
    </g>
  </svg>

  <div class="label label--top">Top<br>Folding</div>
  <div class="label label--front">Front<br>Side</div>
  <div class="label label--back">Back Side</div>
</main>
</body>
</html>
```